K SPIRES Business Card Design

Need a business card design for K Spires, we're a tower company - our main scope of work is to upgrade cellular sites: swap antennas, install new coax, fiber, replace mounts, etc. Mostly tower work.

would like to see a sharp business card design with our logo either on background or with tower image on the background - something describing our field not only in words but in images.

Target Market(s)

USA

Industry/Entity Type

Business

Contact Information for Business Card

Tarnek Obliva
Operations Manager
K Spires LLC

cell 555-318-2094
tarnek@k-spires-example.com

4185 Wexbridge Commerce Pkwy, Suite D
Norcross, GA, 30571

Requirements
Must have
• some tower related design
Nice to have
• some tower or cellular antennas on the background, if possible to compliment our logo...

```html
<!DOCTYPE html>
<html lang="en">
<head>
<meta charset="utf-8">
<title>K Spires Business Card</title>
<link rel="stylesheet" href="https://fonts.googleapis.com/css2?family=Open+Sans:wght@400;600;700&display=swap">
<style>
  :root {
    --page-bg: #e9e6e1;
    --green: #3a9140;
    --navy: #2e2d86;
    --logo-faint: #4f9f8e;
    --ink: #1b1b1b;
    --title-blue: #4a4fb0;
    --contact-ink: #151515;
    --icon-blue: #2f3192;
    --card-light: #eef4fb;
    --card-mid: #b9d1ee;
    --sky: #7fa9df;
    --steel: #6f7a86;
  }
  * { box-sizing: border-box; margin: 0; padding: 0; }
  html, body {
    width: 1200px; height: 900px; overflow: hidden;
    background: var(--page-bg);
    font-family: "Open Sans", Arial, sans-serif;
  }
  .sheet {
    width: 1200px; height: 900px;
    display: flex; align-items: center; justify-content: center; gap: 40px;
  }
  .card {
    width: 540px; height: 310px; position: relative; overflow: hidden;
    box-shadow: 0 6px 18px rgba(0,0,0,.18);
  }
  .card-back {
    background: linear-gradient(150deg, var(--green) 0%, var(--green) 28%, #2f6f72 52%, var(--navy) 75%, var(--navy) 100%);
    display: flex; align-items: center; justify-content: center;
  }
  .brand-name { font-weight: 600; letter-spacing: 1px; white-space: nowrap; }
  .card-back .brand-name { color: var(--logo-faint); font-size: 58px; }
  .card-front {
    background: radial-gradient(ellipse at 30% 40%, var(--card-light) 0%, #d6e5f6 45%, var(--card-mid) 100%);
  }
  .tower-photo {
    position: absolute; top: 0; right: 0; width: 250px; height: 230px;
    background: linear-gradient(215deg, var(--sky) 0%, #9fc0e8 35%, #8d99a6 65%, #55606c 100%);
    clip-path: polygon(30% 0, 100% 0, 100% 100%, 75% 100%, 0 25%);
  }
  .person { position: absolute; left: 38px; top: 86px; }
  .person-name { font-size: 21px; font-weight: 700; color: var(--ink); line-height: 1.15; }
  .person-title { font-size: 14px; color: var(--title-blue); }
  .card-front .brand-name {
    position: absolute; left: 175px; top: 122px;
    font-size: 40px; line-height: 1; color: var(--navy);
  }
  .contacts {
    position: absolute; left: 120px; top: 196px; list-style: none;
    font-size: 13px; color: var(--contact-ink); line-height: 24px;
  }
  .contacts li { display: flex; align-items: center; gap: 10px; white-space: nowrap; }
  .contacts svg { width: 13px; height: 13px; flex: none; fill: var(--icon-blue); stroke: var(--icon-blue); }
  .contacts .no-icon { padding-left: 23px; }
</style>
</head>
<body>
<main class="sheet">
  <section class="card card-back">
    <span class="brand-name">K Spires</span>
  </section>

  <section class="card card-front">
    <div class="tower-photo" role="img" aria-label="Photo of a steel lattice cell tower with antennas and a climber against blue sky"></div>
    <div class="person">
      <p class="person-name">Tarnek Obliva</p>
      <p class="person-title">Operations Manager</p>
    </div>
    <span class="brand-name">K Spires</span>
    <ul class="contacts">
      <li><svg viewBox="0 0 12 12"><rect x="3" y="0.5" width="6" height="11" rx="1" fill="none" stroke-width="1.2"/></svg>555-318-2094</li>
      <li><svg viewBox="0 0 12 12"><rect x="0.5" y="2" width="11" height="8" stroke="none"/><path d="M1 3 L6 7 L11 3" fill="none" stroke="#fff" stroke-width="1"/></svg>tarnek@k-spires-example.com</li>
      <li><svg viewBox="0 0 12 12"><path d="M6 11.5 C3 7.5 2 6 2 4.5 a4 4 0 0 1 8 0 C10 6 9 7.5 6 11.5Z" stroke="none"/><circle cx="6" cy="4.5" r="1.5" fill="#fff" stroke="none"/></svg>4185 Wexbridge Commerce Pkwy, Suite D</li>
      <li class="no-icon">Norcross, GA, 30571</li>
    </ul>
  </section>
</main>
</body>
</html>
```